LM-Steuerberatung WordPress Site fully implemented (tax advisor)

Hello!
I need a little Wordpress Site for my newly founded Tax-Advisor Company.
I am a one-man Office advising in the area of Crypto-Currency.
PLEASE only provide a Design, if you can also Implement a WP-Site afterwards on an existing Webspace.

Please find the Content and Website-Description in the attached Document

Language for the Website is German (for now)

Target Market(s)

Tax-Advisory (specialized in Crypto Currency)

Coding

Coded - Design and coding required

Number of Pages Required

5+ page

Font styles to use
Sans Serif

Requirements
Must have
• Wordpress Implementation afterwards - Details according to attached Project Information Document

```html
<!DOCTYPE html>
<html lang="de">
<head>
<meta charset="utf-8">
<title>LM-Steuerberatung – Home</title>
<link rel="stylesheet" href="https://fonts.googleapis.com/css2?family=Arimo:wght@400;700&display=swap">
<style>
  :root {
    --navy-top: #1c2a45;
    --navy: #121a2e;
    --navy-deep: #0c1222;
    --white: #ffffff;
    --ink: #1d2433;
    --brand-blue: #0000ff;
    --brand-blue-soft: #6a6cff;
    --pill-bg: #ececec;
    --warm-tone: rgba(120, 84, 52, 0.45);
    --flag-black: #111111;
    --flag-red: #dd0000;
    --flag-gold: #ffce00;
  }
  * { box-sizing: border-box; margin: 0; padding: 0; }
  html, body { width: 1200px; height: 843px; overflow: hidden; }
  body { font-family: "Arimo", Arial, sans-serif; background: var(--navy); position: relative; }

  .top-bar { position: absolute; left: 0; top: 0; width: 1200px; height: 32px; background: var(--navy-top); }

  .site-header { position: absolute; left: 0; top: 32px; width: 1200px; height: 91px; background: var(--white); }
  .brand { position: absolute; left: 115px; top: 26px; display: flex; align-items: center; gap: 12px;
           font-size: 21px; font-weight: 700; letter-spacing: 1px; color: var(--ink); }
  .brand-square { width: 38px; height: 38px; background: var(--ink); }

  .main-nav a { position: absolute; top: 36px; font-size: 21px; color: var(--ink); text-decoration: none; letter-spacing: 0.5px; }
  .main-nav .active { font-weight: 700; }
  .nav-home { left: 508px; }
  .nav-services { left: 616px; }
  .nav-about { left: 784px; }
  .nav-contact { left: 931px; }
  .nav-services svg { margin-left: 4px; vertical-align: middle; }

  .lang-switch { position: absolute; left: 1052px; top: 26px; width: 84px; height: 42px; border-radius: 21px;
                 background: var(--pill-bg); display: flex; align-items: center; padding-left: 6px; gap: 8px;
                 font-size: 16px; font-weight: 700; color: var(--ink); }
  .flag { width: 30px; height: 30px; border-radius: 50%; overflow: hidden;
          background: linear-gradient(var(--flag-black) 0 33%, var(--flag-red) 33% 66%, var(--flag-gold) 66%); }

  .hero { position: absolute; left: 0; top: 123px; width: 1200px; height: 720px; overflow: hidden;
          background: radial-gradient(circle at 80% 40%, #1b2740, var(--navy-deep) 70%); }
  .hero-photo { position: absolute; left: 0; top: 0; width: 580px; height: 720px;
                background: linear-gradient(90deg, var(--warm-tone), rgba(18, 26, 46, 0)); }
  .hero-curve { position: absolute; left: 0; top: 0; }

  .hero-title { position: absolute; left: 626px; top: 160px; color: var(--white); font-size: 35px; line-height: 53px; }
  .hero-title strong { display: block; font-size: 35px; }
  .hero-lead { position: absolute; left: 630px; top: 272px; width: 380px; color: var(--white); font-size: 20px; line-height: 30.5px; }
  .hero-cta { position: absolute; left: 615px; top: 390px; width: 309px; height: 54px; border-radius: 27px;
              background: var(--brand-blue); color: var(--white); font-size: 18px; display: flex; align-items: center;
              padding-left: 19px; gap: 12px; text-decoration: none; }
  .hero-cta span { text-decoration: underline; text-underline-offset: 3px; }
  .hero-quote { position: absolute; left: 619px; top: 481px; border-left: 2px solid var(--white); padding-left: 18px;
                color: var(--white); font-size: 23px; line-height: 38px; letter-spacing: 0.6px; }

  .slider-dots { position: absolute; left: 546px; top: 660px; display: flex; align-items: center; gap: 14px; }
  .dot { width: 11px; height: 11px; border-radius: 50%; background: var(--white); }
  .dot.current { width: 20px; height: 20px; border: 2px solid var(--white); background: var(--white);
                 box-shadow: inset 0 0 0 3px var(--navy-deep); }
</style>
</head>
<body>
  <div class="top-bar"></div>

  <header class="site-header">
    <div class="brand"><span class="brand-square"></span>LM STEUERBERATUNG</div>
    <nav class="main-nav">
      <a class="nav-home active" href="#">Home</a>
      <a class="nav-services" href="#">Leistungen<svg width="12" height="8" viewBox="0 0 12 8"><path d="M1 1l5 5 5-5" stroke="#1d2433" stroke-width="2" fill="none"/></svg></a>
      <a class="nav-about" href="#">Über mich</a>
      <a class="nav-contact" href="#">Kontakt</a>
    </nav>
    <div class="lang-switch"><span class="flag"></span>GER</div>
  </header>

  <section class="hero">
    <div class="hero-photo" role="img" aria-label="Foto: Hand hält eine goldene Krypto-Münze"></div>

    <svg class="hero-curve" width="1200" height="720" viewBox="0 0 1200 720">
      <path d="M1200 467 C1180 600 1080 700 950 720 L1200 720 Z" fill="var(--brand-blue)"/>
      <path d="M1200 650 C1170 690 1120 712 1060 720 L1200 720 Z" fill="var(--brand-blue-soft)"/>
    </svg>

    <h1 class="hero-title">Willkommen bei<strong>LM-STEUERBERATUNG!</strong></h1>
    <p class="hero-lead">Ihrem Spezialisten bei allen steuerlichen Themen rund um Einkünfte &amp; Vermögen aus Krypto-Assets.</p>
    <a class="hero-cta" href="#"><span>Weiter zu unseren Leistungen</span>
      <svg width="18" height="10" viewBox="0 0 18 10"><path d="M0 5h16M12 1l4 4-4 4" stroke="#fff" stroke-width="1.5" fill="none"/></svg></a>
    <blockquote class="hero-quote">Dann melde ich einfach meinen<br>Hauptwohnsitz in Österreich ab</blockquote>

    <div class="slider-dots">
      <span class="dot"></span><span class="dot current"></span><span class="dot"></span><span class="dot"></span>
    </div>
  </section>
</body>
</html>
```